Business card for a new cabinet shop company named Veloran Cabinets for high end cabinets

Design a business card, thinking dark rich green with colours to speak of high end luxury ie; cream, gold, black possibly

Mitchell Tarrowby
Director Craftsman
Email: info@veloranjoinery-example.com.au
Instagram : @veloran.cabinets

```html
<!DOCTYPE html>
<html lang="en">
<head>
<meta charset="utf-8">
<title>Veloran Cabinets – Business Card</title>
<link rel="stylesheet" href="https://fonts.googleapis.com/css2?family=Montserrat:wght@400;500;700&display=swap">
<style>
  :root {
    --backdrop: #949494;
    --gold: #c9a65a;
    --gold-light: #d8bc7e;
    --gold-deep: #b8934a;
    --forest: #1f3d2f;
    --paper: #ffffff;
  }
  * { margin: 0; padding: 0; box-sizing: border-box; }
  html, body {
    width: 1200px;
    height: 1108px;
    overflow: hidden;
    background: var(--backdrop);
    font-family: "Montserrat", Arial, sans-serif;
  }
  .card {
    position: absolute;
    left: 242px;
    width: 715px;
    height: 409px;
    border-radius: 30px;
    overflow: hidden;
  }
  .card-back {
    top: 119px;
    background: linear-gradient(115deg, var(--gold) 0%, var(--gold-deep) 35%, var(--gold-light) 52%, var(--gold) 70%, var(--gold-deep) 100%);
  }
  .card-front {
    top: 581px;
    background: var(--paper);
  }
  .brand {
    position: absolute;
    left: 42px;
    top: 0;
    height: 408px;
    display: flex;
    align-items: center;
    gap: 12px;
  }
  .brand-mark {
    width: 22px;
    height: 22px;
    background: var(--forest);
  }
  .brand-name {
    font-weight: 500;
    font-size: 30px;
    color: var(--gold);
    letter-spacing: 0.3px;
    white-space: nowrap;
  }
  .divider {
    position: absolute;
    left: 356px;
    top: 81px;
    width: 2px;
    height: 247px;
    background: var(--gold);
  }
  .details {
    position: absolute;
    left: 380px;
    top: 82px;
    color: var(--forest);
  }
  .person-name {
    font-weight: 700;
    font-size: 33px;
    line-height: 1;
    color: var(--gold);
    white-space: nowrap;
  }
  .person-title {
    font-size: 18px;
    margin-top: 10px;
  }
  .address {
    font-size: 18px;
    line-height: 28px;
    margin-top: 16px;
  }
  .contacts {
    list-style: none;
    margin-top: 10px;
  }
  .contacts li {
    display: flex;
    align-items: center;
    gap: 8px;
    font-size: 15.5px;
    height: 28.5px;
    white-space: nowrap;
  }
  .contacts svg {
    width: 15px;
    height: 15px;
    flex: none;
    fill: var(--gold);
  }
</style>
</head>
<body>
  <section class="card card-back" role="img" aria-label="Gold foil card back with an embossed repeating brand pattern"></section>

  <section class="card card-front">
    <div class="brand">
      <span class="brand-mark"></span>
      <span class="brand-name">Veloran Cabinets</span>
    </div>
    <div class="divider"></div>
    <div class="details">
      <h1 class="person-name">Mitchell Tarrowby</h1>
      <p class="person-title">Director Craftsman</p>
      <p class="address">Your address, City<br>State, Zip 1234</p>
      <ul class="contacts">
        <li>
          <svg viewBox="0 0 16 16"><path d="M1 7c0-3 3-4 7-4s7 1 7 4v1h-4V6H5v2H1z"/><path d="M3 9h10l1 5H2z"/></svg>
          123 456 789
        </li>
        <li>
          <svg viewBox="0 0 16 16"><path d="M1 3h14v1L8 9 1 4z"/><path d="M1 6l7 5 7-5v7H1z"/></svg>
          info@veloranjoinery-example.com.au
        </li>
        <li>
          <svg viewBox="0 0 16 16"><circle cx="8" cy="8" r="6.5" fill="none" stroke="var(--gold)" stroke-width="2"/></svg>
          @veloran.cabinets
        </li>
        <li>
          <svg viewBox="0 0 16 16"><circle cx="8" cy="8" r="7" fill="none" stroke="var(--gold)" stroke-width="1.6"/><path d="M1 8h14M8 1c-3 3-3 11 0 14M8 1c3 3 3 11 0 14" fill="none" stroke="var(--gold)" stroke-width="1.2"/></svg>
          www.veloranjoinery-example.com.au
        </li>
      </ul>
    </div>
  </section>
</body>
</html>
```